Unique Business Card Design

Unique Business Card design for our orthotic and prosthetic company. Our logo is on our website, color is light blue. Unique shape (artificial leg shaped, vertical, etc..) preferred. Logo, business name, individual name and basic demographics needed.

Industry/Entity Type

Business

Contact Information for Business Card

Logo, Industry, Phone # Logo, "Prosthetic & Orthotic Services" Place to add individual name and contact info

Colors
cee9f5

Requirements
Must have
• The icon must be there, placement of "Prosthetic & Orthotic Services" can be moved
Nice to have
• Like the mix of light blue, and a little darker blue. One design included the icons from my website which was a nice touch

```html
<!DOCTYPE html>
<html lang="en">
<head>
<meta charset="utf-8">
<title>Limbwell Inc. Business Card</title>
<link rel="stylesheet" href="https://fonts.googleapis.com/css2?family=Open+Sans:wght@400;600;700&display=swap">
<style>
  :root {
    --brand-blue: #2a6cc4;
    --brand-blue-deep: #1d57a8;
    --card-white: #ffffff;
    --stage: #2b2b2b;
    --curve-shadow: #c9ced6;
    --ink-white: #ffffff;
  }
  * { margin: 0; padding: 0; box-sizing: border-box; }
  html, body { width: 1200px; height: 950px; overflow: hidden; }
  body {
    background: var(--stage);
    font-family: "Open Sans", Arial, sans-serif;
    display: flex;
    flex-direction: column;
    align-items: center;
    justify-content: center;
    gap: 40px;
  }
  .card {
    position: relative;
    width: 760px;
    height: 434px;
    border-radius: 26px;
    overflow: hidden;
  }
  /* Front */
  .card-front { background: var(--brand-blue); }
  .front-brand {
    position: absolute;
    left: 140px; top: 130px;
    display: flex; align-items: center; gap: 34px;
  }
  .brand-dot {
    width: 120px; height: 120px; border-radius: 50%;
    background: var(--card-white);
    flex: none;
  }
  .brand-dot.is-blue { background: var(--brand-blue); }
  .brand-name {
    font-weight: 700; font-size: 40px; letter-spacing: 0.5px;
    line-height: 1;
    padding-bottom: 8px;
    border-bottom: 3px solid currentColor;
  }
  .brand-tagline { font-size: 21px; margin-top: 8px; }
  .front-brand .brand-name, .front-brand .brand-tagline { color: var(--ink-white); }
  .front-web {
    position: absolute; left: 0; right: 0; bottom: 84px;
    display: flex; align-items: center; justify-content: center; gap: 16px;
    color: var(--ink-white); font-size: 15px; letter-spacing: 0.5px;
  }
  .front-web .rule { width: 150px; height: 1px; background: rgba(255,255,255,0.8); }
  .front-rule-top {
    position: absolute; left: 320px; right: 130px; top: 262px;
    height: 1px; background: rgba(255,255,255,0.8);
  }
  /* Back */
  .card-back { background: var(--card-white); }
  .back-wave { position: absolute; inset: 0; }
  .back-brand {
    position: absolute; left: 90px; top: 60px;
    display: flex; align-items: center; gap: 26px;
  }
  .back-brand .brand-dot { width: 108px; height: 108px; }
  .back-brand .brand-name { color: var(--brand-blue); font-size: 36px; }
  .back-brand .brand-tagline { color: var(--brand-blue); font-size: 19px; }
  .contact-list {
    position: absolute; right: 34px; top: 196px;
    list-style: none; text-align: right;
    color: var(--ink-white); font-size: 17px; line-height: 27px;
  }
  .contact-list li { display: flex; align-items: center; justify-content: flex-end; gap: 10px; }
  .contact-list svg { width: 16px; height: 16px; fill: var(--ink-white); flex: none; }
  .contact-list .email { margin-top: 14px; }
  .person {
    position: absolute; left: 40px; bottom: 34px;
    color: var(--ink-white);
  }
  .person-name { font-size: 26px; font-weight: 700; line-height: 1.3; }
  .person-title { font-size: 17px; font-weight: 600; margin-bottom: 10px; }
  .person-address { font-size: 17px; line-height: 24px; font-style: normal; }
</style>
</head>
<body>
  <section class="card card-front" aria-label="Card front">
    <div class="front-brand">
      <div class="brand-dot" aria-hidden="true"></div>
      <div>
        <div class="brand-name">LIMBWELL INC.</div>
        <div class="brand-tagline">Prosthetic &amp; Orthotic Services</div>
      </div>
    </div>
    <div class="front-rule-top"></div>
    <div class="front-web">
      <span class="rule"></span><span>www.limbwellinc.com</span><span class="rule"></span>
    </div>
  </section>

  <section class="card card-back" aria-label="Card back">
    <svg class="back-wave" viewBox="0 0 760 434" preserveAspectRatio="none" aria-hidden="true">
      <path d="M0,242 C300,237 560,207 760,32 L760,44 C560,219 300,249 0,254 Z" fill="var(--curve-shadow)"/>
      <path d="M0,250 C300,245 560,215 760,40 L760,434 L0,434 Z" fill="var(--brand-blue)"/>
    </svg>
    <div class="back-brand">
      <div class="brand-dot is-blue" aria-hidden="true"></div>
      <div>
        <div class="brand-name">LIMBWELL INC.</div>
        <div class="brand-tagline">Prosthetic &amp; Orthotic Services</div>
      </div>
    </div>
    <ul class="contact-list">
      <li>555.210.4400
        <svg viewBox="0 0 16 16" aria-hidden="true"><path d="M2 5c0-2 2-3 6-3s6 1 6 3v1h-3V5H5v1H2z M4 7h8l2 7H2z"/></svg>
      </li>
      <li>555.210.4401
        <svg viewBox="0 0 16 16" aria-hidden="true"><path d="M4 1h8v14H4z M5 3v9h6V3z"/></svg>
      </li>
      <li>555-3086120
        <svg viewBox="0 0 16 16" aria-hidden="true"><path d="M4 1h8v4H4z M1 6h14v7h-3v2H4v-2H1z M5 10v4h6v-4z"/></svg>
      </li>
      <li class="email">mfeldstein@limbwellinc.com
        <svg viewBox="0 0 16 16" aria-hidden="true"><path d="M1 3h14v10H1z M2 4l6 5 6-5z" fill-rule="evenodd"/></svg>
      </li>
    </ul>
    <div class="person">
      <div class="person-name">Mara Feldstein</div>
      <div class="person-title">CO LPO</div>
      <address class="person-address">2380 Avenue R<br>Brooklyn, NY 11229</address>
    </div>
  </section>
</body>
</html>
```